Bookcover: Ways to Turn Into a Bold Pathfinder

I am publishing a super-low-cost innovation book for €4,99 on Quillmere Open Press to help everyone become a great innovator: young ambitious people without college education nor a big budget. Do you want to help me?

Brief:
Design a book cover 1600 x 2560 pixels for QOP.
Main title: Ways to Turn Into a Bold Pathfinder
Sub title: mindset - insights - skills & tools
Author: Joost ter Brakel
Design: captive, and appealing to everyone
Target Group: young ambitious people without college education

For quillmere please format the height/width ratio of 1.6:1

```html
<!DOCTYPE html>
<html lang="en">
<head>
<meta charset="UTF-8">
<title>Ways to Turn Into a Bold Pathfinder — Book Cover</title>
<link href="https://fonts.googleapis.com/css2?family=Oswald:wght@500;600;700&display=swap" rel="stylesheet">
<style>
  :root {
    --page-bg: #e4e3e0;
    --teal: #3a9aa8;
    --mist: #cdd7de;
    --indigo: #37388a;
    --sky: #3d93cf;
    --mid-blue: #4f73b0;
    --ink-light: #f2f1ee;
  }
  * { margin: 0; padding: 0; box-sizing: border-box; }
  html, body {
    width: 1200px;
    height: 900px;
    overflow: hidden;
    background: var(--page-bg);
  }
  .stage {
    position: relative;
    width: 1200px;
    height: 900px;
    display: flex;
    align-items: center;
    justify-content: center;
  }
  .book-cover {
    position: relative;
    width: 512px;
    height: 820px;
    overflow: hidden;
    background:
      radial-gradient(ellipse 70% 55% at 95% 8%, var(--mist) 0%, rgba(205,215,222,0) 100%),
      radial-gradient(ellipse 80% 60% at 100% 95%, var(--sky) 0%, rgba(61,147,207,0) 100%),
      radial-gradient(ellipse 75% 55% at 0% 0%, var(--teal) 0%, rgba(58,154,168,0) 100%),
      linear-gradient(180deg, var(--mid-blue) 0%, var(--indigo) 100%);
    color: var(--ink-light);
    font-family: "Oswald", "Arial Narrow", sans-serif;
  }
  .book-title {
    position: absolute;
    top: 130px;
    left: 0;
    right: 0;
    text-align: center;
    font-weight: 700;
    font-size: 92px;
    line-height: 1.06;
    letter-spacing: 0.5px;
    text-transform: uppercase;
  }
  .book-title span { display: block; }
  .book-subtitle {
    position: absolute;
    top: 580px;
    left: 0;
    right: 0;
    text-align: center;
    font-weight: 500;
    font-size: 24px;
    letter-spacing: 1.5px;
    text-transform: uppercase;
  }
  .book-author {
    position: absolute;
    bottom: 62px;
    left: 0;
    right: 0;
    text-align: center;
    font-weight: 600;
    font-size: 30px;
    letter-spacing: 0.3px;
  }
</style>
</head>
<body>
  <main class="stage">
    <section class="book-cover">
      <h1 class="book-title">
        <span>Ways to</span>
        <span>Turn Into</span>
        <span>A Bold</span>
        <span>Pathfinder</span>
      </h1>
      <p class="book-subtitle">mindset - insights - skills &amp; tools</p>
      <p class="book-author">Joost ter Brakel</p>
    </section>
  </main>
</body>
</html>
```